Dietitian needs awesome business card

I need a contemporary design that's eye catching but professional.
My card is to given to doctors, specialists and patients alike.
I manage patients with chronic diseases
I have uploaded my logo and current business card, I would also like the other Certified Clinical Nutritionist logo incorporated into the design

Target Market(s)

Doctors, specialists and patients

Industry/Entity Type

Healthcare

Contact Information for Business Card

www.brightfieldnutrition.com.au
Ph: 0427 561 903
Fax: 6457 2183
email: marcus.k.diet@fernmail.com
Space on the back of the card with: Appointment date, Appointment time and appointment location

Font styles to use
Serif

Colors
fbee3e
876aae
ffc214

Requirements
Must have
• My Logo
• Certified Clinical Nutritionist Logo
• My 4 locations - Pinebrook Medical Centre, North Corrin Health, Hollis Medical, Ashcombe Doctors Surgery
Nice to have
• I like the colours in my current business card

```html
<!DOCTYPE html>
<html lang="en">
<head>
<meta charset="utf-8">
<title>Brightfield Nutrition &amp; Dietetics – Business Card</title>
<link rel="stylesheet" href="https://fonts.googleapis.com/css2?family=Lora:wght@400;500&display=swap">
<style>
  :root {
    --page-bg: #2b2b2b;
    --card-bg: #ffffff;
    --brand-blue: #1f3a9c;
    --brand-green: #8cc63f;
    --ink-grey: #5a5a5a;
    --rule-grey: #bdbdbd;
    --badge-fill: #eef1f6;
    --badge-edge: #c9cfdb;
    --wash-light: #f2f5ef;
    --wash-mid: #e3eadc;
  }
  * { box-sizing: border-box; margin: 0; padding: 0; }
  html, body {
    width: 1200px; height: 886px; overflow: hidden;
    background: var(--page-bg);
    font-family: "Lora", "Georgia", serif;
  }
  .stage {
    width: 1200px; height: 886px;
    display: flex; justify-content: center; align-items: center; gap: 64px;
  }
  .card {
    position: relative;
    width: 428px; height: 700px;
    background: var(--card-bg);
    border-radius: 26px;
    overflow: hidden;
  }
  .brand {
    display: flex; align-items: center; gap: 12px;
    color: var(--brand-blue);
    font-weight: 500;
  }
  .brand-dot {
    width: 40px; height: 40px; border-radius: 50%;
    background: var(--brand-green); flex: none;
  }

  /* Back: appointment side */
  .card-back .backdrop {
    position: absolute; inset: 0;
    background: radial-gradient(ellipse at 70% 45%, var(--wash-mid), var(--wash-light) 55%, var(--card-bg) 90%);
  }
  .card-back .content { position: relative; padding: 44px 40px; height: 100%; }
  .card-back .brand { font-size: 20px; line-height: 1.2; }
  .card-back .brand-name { max-width: 240px; }
  .appt-field {
    display: flex; align-items: flex-end; gap: 10px;
    margin-top: 34px; color: var(--brand-blue); font-size: 16px;
  }
  .appt-field .fill { flex: 1; border-bottom: 1px solid var(--rule-grey); height: 20px; }
  .appt-field .suffix { font-size: 12px; }
  .notes { margin-top: 34px; }
  .notes span { display: block; height: 40px; border-bottom: 1px solid var(--rule-grey); }
  .locations {
    position: absolute; left: 40px; bottom: 44px;
    list-style: none; color: var(--ink-grey); font-size: 14px; line-height: 1.7;
  }
  .locations li::before {
    content: ""; display: inline-block; width: 11px; height: 11px;
    border: 1px solid var(--brand-blue); margin-right: 10px; vertical-align: -1px;
  }

  /* Front: contact side */
  .card-front .brand { position: absolute; top: 40px; right: 40px; font-size: 17px; }
  .credential-badge {
    position: absolute; top: 36px; left: 44px;
    width: 48px; height: 48px; border-radius: 50%;
    background: var(--badge-fill); border: 2px solid var(--badge-edge);
  }
  .contact { position: absolute; left: 44px; bottom: 48px; }
  .contact .name { color: var(--brand-blue); font-size: 28px; font-weight: 400; }
  .contact .role { color: var(--brand-green); font-size: 19px; margin-bottom: 16px; }
  .contact .line { color: var(--ink-grey); font-size: 17px; line-height: 1.45; }
  .contact .line b { color: var(--brand-green); font-weight: 400; }
</style>
</head>
<body>
<main class="stage">
  <section class="card card-back">
    <div class="backdrop" role="img" aria-label="Soft faded photograph of green leaves"></div>
    <div class="content">
      <div class="brand"><span class="brand-dot"></span><span class="brand-name">Brightfield Nutrition &amp; Dietetics</span></div>
      <div class="appt-field"><span>Date :</span><span class="fill"></span></div>
      <div class="appt-field"><span>Time :</span><span class="fill"></span><span class="suffix">AM/PM</span></div>
      <div class="notes"><span></span><span></span><span></span><span></span></div>
      <ul class="locations">
        <li>Pinebrook Medical Centre</li>
        <li>North Corrin Health</li>
        <li>Ashcombe Doctors Surgery</li>
        <li>Hollis Medical</li>
      </ul>
    </div>
  </section>

  <section class="card card-front">
    <div class="credential-badge" role="img" aria-label="Certified Clinical Nutritionist accreditation badge"></div>
    <div class="brand"><span class="brand-dot"></span><span>Brightfield</span></div>
    <div class="contact">
      <p class="name">Marcus Kellaway</p>
      <p class="role">Nutritionist &amp; Chef</p>
      <p class="line"><b>p.</b>0427 561 903</p>
      <p class="line"><b>f.</b>6457 2183</p>
      <p class="line">marcus.k.diet@fernmail.com</p>
      <p class="line">brightfieldnutrition.com.au</p>
    </div>
  </section>
</main>
</body>
</html>
```